Bref créative
Kivoraly Granola Label
Front & Back Package Label
We are a new, small granola company looking for a front and back label for our retail package.
Food
Retail Market
We would like an eye catching label based on our current logo.
Logo file
front text only (not layout) for design
back text only (not layout) for design
Bag the product will be packed in.

```html
<!DOCTYPE html>
<html lang="en">
<head>
<meta charset="utf-8">
<title>Kivoraly Granola – Package Labels</title>
<link rel="stylesheet" href="https://fonts.googleapis.com/css2?family=Kaushan+Script&family=Crimson+Text:wght@400;600&display=swap">
<style>
  :root {
    --page: #ffffff;
    --film: #eceeef;
    --film-edge: #d3d6d8;
    --seal: #c9cccf;
    --granola-light: #b98a58;
    --granola-mid: #8d5a2f;
    --granola-dark: #5e3718;
    --kraft: #ead9b6;
    --kraft-edge: #cdb68a;
    --green: #4f7a1f;
    --brown: #5a3417;
    --ink: #3a2a18;
  }
  * { box-sizing: border-box; margin: 0; padding: 0; }
  html, body { width: 1200px; height: 686px; overflow: hidden; background: var(--page); }
  .canvas { position: relative; width: 1200px; height: 686px; }

  .bag {
    position: absolute; top: 24px; width: 548px; height: 636px;
    border-radius: 10px; overflow: hidden;
    background: var(--film); border: 1px solid var(--film-edge);
  }
  .bag--front { left: 30px; }
  .bag--back { left: 620px; }
  .bag__seal {
    position: absolute; left: 0; right: 0; top: 18px; height: 10px;
    background: var(--seal);
  }
  .bag__fill {
    position: absolute; left: 0; right: 0; top: 118px; bottom: 0;
    background: radial-gradient(circle at 30% 30%, var(--granola-light), var(--granola-mid) 55%, var(--granola-dark));
  }

  .label {
    position: absolute; background: var(--kraft);
    border: 1px solid var(--kraft-edge);
    box-shadow: 0 3px 8px rgba(0,0,0,.35);
    color: var(--ink);
  }
  .label--front { left: 44px; top: 150px; width: 460px; height: 420px; transform: rotate(-1deg); text-align: center; }
  .label--back { left: 40px; top: 140px; width: 468px; height: 460px; padding: 18px 26px; }

  .script { font-family: "Kaushan Script", cursive; }
  .serif { font-family: "Crimson Text", Georgia, serif; }

  .tagline { position: absolute; left: 24px; top: 20px; font-size: 28px; color: var(--green); transform: rotate(-6deg); }
  .brand-name {
    position: absolute; left: 0; right: 0; top: 90px;
    font-size: 76px; line-height: 1; color: var(--green);
  }
  .brand-name--sub { top: 170px; font-size: 56px; }
  .claim { position: absolute; left: 0; right: 0; top: 262px; font-size: 24px; color: var(--brown); }
  .blend { position: absolute; left: 0; right: 0; top: 300px; font-size: 30px; line-height: 1.2; color: var(--green); }
  .net-weight { position: absolute; left: 20px; bottom: 12px; font-size: 16px; color: var(--brown); }

  .allergen { text-align: center; font-size: 19px; font-weight: 600; margin-bottom: 8px; }
  .story { font-size: 14.5px; line-height: 1.22; margin-bottom: 10px; }
  .ingredients { font-size: 11px; line-height: 1.25; width: 250px; margin-top: 8px; }
  .company { font-size: 12px; line-height: 1.3; margin-top: 10px; }
  .back-brand { position: absolute; right: 30px; top: 300px; font-size: 30px; color: var(--green); line-height: 1; text-align: right; }
  .back-tagline { position: absolute; right: 30px; bottom: 24px; font-size: 26px; color: var(--green); }
</style>
</head>
<body>
<main class="canvas">

  <section class="bag bag--front" aria-label="Front of package">
    <div class="bag__seal"></div>
    <div class="bag__fill" role="img" aria-label="Granola visible through the clear bag"></div>
    <div class="label label--front">
      <p class="tagline script">Simply Decadent!</p>
      <p class="brand-name script">Kivoraly</p>
      <p class="brand-name brand-name--sub script">Granola</p>
      <p class="claim serif">Naturally Gluten Free</p>
      <p class="blend script">Chef's Original Blend<br>with Fruits &amp; Nuts</p>
      <p class="net-weight serif">Net. Weight 12 Ounces</p>
    </div>
  </section>

  <section class="bag bag--back" aria-label="Back of package">
    <div class="bag__seal"></div>
    <div class="bag__fill" role="img" aria-label="Granola visible through the clear bag"></div>
    <div class="label label--back serif">
      <p class="allergen">Allergen Information: Contains Nuts</p>
      <p class="story">Why is Kivoraly Granola simply decadent? Because it's made with the best ingredients and artfully baked in small batches. It is just sweet enough without being high in sugar and it is gluten free without using ingredients that are difficult to pronounce. This is food that your great grandmother would recognize as food. It's not made in a flavor factory, nothing artificial, no chemical preservatives. It's made by a chef who understands that eating well does not mean you have to sacrifice flavor or enjoyment.</p>
      <p class="story">Kivoraly Granola will make you look forward to eating breakfast everyday. In fact it is so delicious you may find yourself eating it for lunch and dinner too! Go ahead, we won't judge.</p>
      <p class="ingredients">Ingredients: Certified Gluten Free Oats, Organic Unsweetened Coconut, Organic Dried Apples, Organic Dried Cranberries, Organic Almonds, Organic Flax Seed Meal, Honey, Organic Brown Sugar, Extra Virgin Olive Oil, Sea Salt.</p>
      <p class="company">Kivoraly Granola Company<br>Loon Cove, ME<br>info@kivoraly.com</p>
      <p class="back-brand script">Kivoraly<br>Granola</p>
      <p class="back-tagline script">Simply Decadent!</p>
    </div>
  </section>

</main>
</body>
</html>
```